Logo and Website Design for QR.KA Horizon - a Software Engineering and IT company

Software engineering and IT are two different disciplines - and yet inseparably linked. At QR.KA Horizon, we combine both worlds and ensure that our software solutions are not only innovative and powerful, but also integrate perfectly into existing IT landscapes. Vision stands more for imagination, so it is not neccessary something what has to do with visualisation. Please consider that the winning competitor is also instructed to make a logo for the company. So please make a suitable logo for QR.KA Horizon to which the website fits to and show it during the website creation process. A good Logo desing is important for winning the competition. The website should contain a landing page with inspiring, perhaps futuristic photos of a datacenter and lines of code. Eventuelly flewent integrated in the text. On the landing page the company should introduced with a small text (max 250 words) followed by a section with a short text to one of our products nearby a graphic visualising the architecture of the product. The menue should be on top and fixed during scrolling and consist of the menue items home, solutions, who are we and a contact button. There should be a footer for linking social media, rights and Impressum. Only as an idea not a must. The very first view on the landing page could also be the menue bar and below of it a transparent unsharp photo (e.g. datacenter, lines of code, both ;) with the company name in the center.

###############################################################

Hi Designers,

Despite your very good approaches for describing QR.KA Horizon, here a short introduction (german text) from ourself:

------
QR.KA Horizon – Ihr Partner für ganzheitliche Softwarelösungen

Die QR.KA Horizon ist ein dynamisches Unternehmen, das sich nicht nur auf die Konzeption, das Design und die Entwicklung maßgeschneiderter Software spezialisiert hat, sondern auch deren reibungslosen Betrieb sicherstellt. Mit einem Team aus erfahrenen Softwarearchitekten und IT-Professionals verbinden wir modernste Softwareentwicklung mit tiefgehendem IT-Know-how – für Lösungen, die nachhaltig, leistungsstark und zukunftssicher sind.

Software Engineering trifft IT – Perfektion in Kombination
Software Engineering und IT sind zwei unterschiedliche Disziplinen – und doch untrennbar miteinander verbunden. Wir bei QR.KA Horizon vereinen beide Welten und sorgen dafür, dass unsere Softwarelösungen nicht nur innovativ und leistungsfähig sind, sondern sich auch perfekt in bestehende IT-Landschaften integrieren.

Expertise mit Fokus auf Healthcare & komplexe IT-Umgebungen
Unsere Experten bringen jahrzehntelange Erfahrung aus dem Healthcare-Sektor mit und unterstützen IT-Abteilungen großer Kliniken in der Entwicklung und Optimierung von Softwarelösungen. Von Anwendungssoftware bis hin zu Steuerungssystemen – unsere Softwareingenieure wissen genau, worauf es ankommt.

Ganzheitlicher Ansatz – über die Software hinaus
Wir entwickeln nicht nur Software, sondern übernehmen auch die Verantwortung für deren stabile und effiziente Betriebsumgebung. Egal, ob on-premises, in der Cloud oder als SaaS-Lösung – wir kümmern uns um den kompletten Lifecycle Ihrer Anwendung.

Ihre Vision – unsere Mission.
Ob Neuentwicklung einer SaaS-Anwendung oder die Migration bestehender Lösungen in eine moderne SaaS-Umgebung – mit QR.KA Horizon haben Sie einen starken Partner an Ihrer Seite.

Lassen Sie uns gemeinsam die Zukunft Ihrer Software gestalten!
--------------

Our first solution called "Clear Record Transfer Gateway" (CLURA)
-------------------
Teilen Sie Ihre Daten sicher – ohne Kompromisse!

Sie nutzen eine relationale Datenbank (Brightcask, Tabulon Hub, Vellumdb etc.) und möchten ausgewählte Daten mit Dritten teilen – sei es für ein Data Warehouse, Business Controller, Lieferanten oder Kunden? Doch dabei sollen Datensicherheit, Integrität und Verfügbarkeit Ihrer primären Lösung in keiner Weise gefährdet werden?

Mit unserer Lösung erhalten Sie genau das: Maximalen Schutz für Ihre Anwendung bei gleichzeitigem Nutzen durch autorisierte Dritte – ganz ohne teure Lizenzkosten für eine Schattendatenbank.

Lassen Sie uns gemeinsam herausfinden, wie Sie Ihre Daten sicher und effizient nutzen können. Kontaktieren Sie uns – wir zeigen Ihnen, was möglich ist!
---------------------

Our second solution MIVO:
---------------------
MIVO – Program for a Tone Matching Instrument ist die smarte Lösung für Unternehmen, die bei Farbgenauigkeit keine Kompromisse machen. Die Software erkennt Farbabweichungen zwischen Mustern vollautomatisch, beschreibt sie verständlich und sorgt so für gleichbleibend hohe Produktqualität – schnell, visuell und präzise. Perfekt für alle, die Farbe zur Vertrauenssache machen.
-------------------------

Thanks,
Gerold

Target Market(s)

IT Professionals from any sector

Industry/Entity Type

Healthcare and other

Coding

Coded - Design and coding required

Number of Pages Required

1 page

Font styles to use
Sans Serif

Colors
0054AA
0677BA
7BADD7
CADEEF
E8F1F8
0094D4
00A9DD
6FCCEA
C7EBF8
E9F6FB
00AB8E
00BBA5
67D7C9
C6EFE9
E9F9F6

Requirements
Must have
• Please see description
Nice to have
• On the landing page the company should introduced with a small text (max 250 words) followed by a section with a short text to one of our products nearby a graphic visualising the architecture of the product. The menue should be on top and fixed during scrolling and consist of the menue items home, solutions, who are we and a contact button. There should be a footer for linking social media, rights and Impressum. Only as an idea not a must. The very first view on the landing page could also be the menue bar and below of it a transparent unsharp photo (e.g. datacenter, lines of code, both ;) with the company name in the center.
Should not have
• Please see description

```html
<!DOCTYPE html>
<html lang="en">
<head>
<meta charset="utf-8">
<title>QR.KA Horizon – Software Engineering meets IT</title>
<link href="https://fonts.googleapis.com/css2?family=Sora:wght@400;500;600;700;800&family=Space+Grotesk:wght@400;500;600&display=swap" rel="stylesheet">
<style>
:root{
  --black:#000;
  --ink:#0b0b0b;
  --teal:#00bba5;
  --teal-bright:#1fd0b8;
  --teal-text:#22c4ae;
  --teal-deep:#062f2c;
  --teal-night:#041d1b;
  --mint:#e9f9f6;
  --mint-mid:#67d7c9;
  --grey:#8a8a8a;
  --line:#2a2a2a;
  --white:#fff;
  --head:'Sora',sans-serif;
  --body:'Space Grotesk',sans-serif;
}
*{margin:0;padding:0;box-sizing:border-box}
html,body{width:1200px;height:2922px;overflow:hidden}
body{background:var(--black);color:var(--white);font-family:var(--body);position:relative}
.abs{position:absolute}
.vline{position:absolute;width:1px;background:var(--line)}
.hline{position:absolute;height:1px;background:var(--line)}

/* hero */
.hero-bg{left:0;top:0;width:1200px;height:437px;background:radial-gradient(ellipse at 75% 35%,#1f2624 0%,#0d1110 45%,#020303 100%)}
.nav-logo{left:75px;top:26px;font-family:var(--head);font-size:21px;font-weight:500;color:var(--teal);display:flex;align-items:center;gap:8px}
.nav-logo .mark{width:16px;height:16px;background:var(--teal)}
.nav{left:508px;top:31px;display:flex;gap:29px;font-size:11.5px}
.nav a{color:var(--white);text-decoration:none}
.nav a.active{color:var(--teal-text)}
.nav-contact{left:1083px;top:31px;font-size:11.5px;color:var(--white)}
.eyebrow{font-size:11px;color:var(--teal-text)}
.hero-copy{left:75px;top:126px;width:400px}
.hero-title{margin-top:11px;width:390px;font-family:var(--head);font-weight:700;font-size:21px;line-height:28px;text-transform:uppercase}
.hero-text{margin-top:10px;width:330px;font-size:10.6px;line-height:14.3px;color:#e8e8e8}
.btn{display:flex;align-items:center;gap:10px;background:var(--teal);color:var(--white);font-size:11px;padding-left:12px}
.btn .ico{width:14px;height:14px;position:relative}
.btn .ico i{position:absolute;width:6px;height:6px;background:#fff}
.hero-btn{margin-top:18px;width:122px;height:30px}

/* feature cards */
.cards-strip{left:0;top:437px;width:50px;height:194px;background:var(--teal)}
.feature{top:437px;height:194px;background:var(--teal-deep);padding:22px 25px;overflow:hidden}
.feature h3{font-family:var(--head);font-weight:500;font-size:14.2px;display:flex;align-items:center;gap:10px;text-transform:uppercase}
.feature h3 .ico{width:14px;height:12px;background:var(--white);clip-path:polygon(0 60%,40% 60%,40% 20%,100% 20%,100% 50%,60% 50%,60% 100%,0 100%)}
.feature p{margin-top:33px;font-size:10.5px;line-height:14.3px;color:#e4e4e4;width:325px}
.feature .brand-ghost{position:absolute;right:24px;bottom:14px;font-family:var(--head);font-weight:700;font-size:26px;color:#2d5b57}
.feature.light{background:var(--mint);color:var(--ink)}
.feature.light h3 .ico{background:var(--ink)}
.feature.light p{color:#333;width:280px}
.feature.light .brand-ghost{color:#7edccd}

.scroll{left:1157px;top:460px;writing-mode:vertical-rl;transform:rotate(180deg);font-size:10px;letter-spacing:.3px;color:#ddd}
.scroll-pill{left:1167px;top:577px;width:14px;height:23px;border-radius:7px;background:#d9d9d9}

/* story */
.code-band{left:0;top:631px;width:1200px;height:102px;background:linear-gradient(90deg,#161616,#2b2b2b 30%,#111 70%,#1a1a1a)}
.story-photo{left:0;top:733px;width:387px;height:351px;background:linear-gradient(160deg,#2a2a2a,#111 60%,#1c1c1c)}
.story-panel{left:387px;top:733px;width:763px;height:351px;background:linear-gradient(110deg,#0d4a44,#06302c 55%,#041f1d)}
.side-num{font-family:var(--head);font-weight:700;font-size:27px;writing-mode:vertical-rl;transform:rotate(180deg);color:#d8d8d8}
.dot{position:absolute;width:4px;height:4px;border-radius:50%;background:#ddd}
.ring{position:absolute;width:22px;height:22px}
.section-label{font-family:var(--head);font-size:14.2px;color:var(--teal-text);text-transform:uppercase}
.story-label{left:427px;top:762px}
.story-title{left:427px;top:795px;width:470px;font-family:var(--head);font-weight:500;font-size:19px;line-height:25px}
.story-text{left:427px;top:860px;width:515px;font-size:10.5px;line-height:14.3px;color:#e8e8e8}
.story-text p+p{margin-top:12px}
.story-link{left:738px;top:1036px;font-size:10.5px;font-style:italic;text-transform:uppercase;display:flex;gap:6px;align-items:center}
.strip2{left:0;top:1084px;width:50px;height:59px;background:var(--teal)}
.strip2-photo{left:50px;top:1084px;width:1150px;height:59px;background:linear-gradient(90deg,#141414,#232323 40%,#0e0e0e)}

/* solutions */
.sol-label{left:144px;top:1184px}
.sol-title{left:144px;top:1218px;width:620px;font-family:var(--head);font-weight:500;font-size:19px;line-height:25px}
.sol-card{top:1344px;width:300px;height:316px}
.sol-card .num{font-family:var(--head);font-weight:800;font-size:66px;line-height:66px;color:#3a3a3a;letter-spacing:-2px}
.sol-card h4{margin-top:22px;width:240px;min-height:38px;font-family:var(--head);font-weight:500;font-size:14.2px;line-height:19px;text-transform:uppercase}
.sol-card p{margin-top:38px;font-size:10.5px;line-height:14.3px;color:#e0e0e0}
.sol-card .more{position:absolute;left:0;top:284px;font-size:10px;display:flex;align-items:center;gap:8px}
.sol-card .more i{display:block;width:20px;height:1px;background:#fff;position:relative}
.sol-photo{left:758px;top:1344px;width:317px;height:316px;background:linear-gradient(150deg,#2a8f86,#156b64 50%,#0e4f4a);padding:12px 19px}
.sol-photo .num{color:#5fb9ae}
.sol-photo h4{margin-top:10px}

/* section 4 */
.eng-label{left:134px;top:1788px;width:110px;font-size:11px;line-height:14px;font-weight:600}
.thumb{position:absolute;width:103px;height:67px;border:1px solid #444;background:linear-gradient(135deg,#2a2a2a,#111)}
.eng-more{left:180px;top:1980px;font-size:10.5px}
.eng-drawing{left:300px;top:1818px;width:245px;height:145px;background:radial-gradient(ellipse,#3a3a3a,#0a0a0a 75%)}
.code-label{left:134px;top:2036px;font-size:11px;font-weight:600}
.code-shot{left:134px;top:2058px;width:407px;height:135px;background:#1b2230;border:1px solid #2f3a4d}
.code-shot .bar{position:absolute;height:3px;background:#4a6a8f;border-radius:1px}
.try-btn{left:134px;top:2221px;width:122px;height:28px}
.int-label{left:616px;top:1802px}
.int-title{left:616px;top:1874px;width:480px;font-family:var(--head);font-weight:500;font-size:19px;line-height:25px}
.acc{left:616px;top:2042px;width:460px;border:1px solid #3a3a3a}
.acc-row{height:40px;display:flex;align-items:center;gap:12px;padding-left:16px;font-size:11px;font-weight:600;border-top:1px solid #3a3a3a}
.acc-row:first-child{border-top:none}
.acc-row .sq{width:14px;height:12px;background:var(--teal);transform:skewX(-10deg)}
.acc-row.open{color:var(--teal-text);font-weight:500}
.acc-body{background:var(--teal-deep);padding:10px 16px 10px 52px;font-size:10.5px;line-height:14.3px;color:#e6e6e6;height:76px}
.side-strip{left:1150px;top:1718px;width:50px;height:300px;background:var(--teal)}

/* CTA */
.cta-bg{left:0;top:2321px;width:1200px;height:601px;background:linear-gradient(180deg,#14a697 0%,#19b09f 40%,#0f8f82 100%)}
.city{left:0;top:2321px;width:1200px;height:601px;background:linear-gradient(180deg,rgba(0,0,0,0) 0%,rgba(80,230,210,.12) 60%,rgba(0,60,55,.25) 100%)}
.cta-ghost{left:150px;top:2348px;font-family:var(--head);font-weight:700;font-size:82px;color:rgba(255,255,255,.13);letter-spacing:-1px}
.cta-title{left:153px;top:2500px;width:560px;font-family:var(--head);font-weight:600;font-size:19.5px;line-height:25px}
.cta-btn{left:180px;top:2594px;width:126px;height:30px;background:var(--teal-bright);color:#fff}

/* footer */
.foot-overlay{left:0;top:2674px;width:1200px;height:248px;background:rgba(4,55,52,.55)}
.foot-panel{left:106px;top:2674px;width:282px;height:248px;background:rgba(10,90,84,.55)}
.foot-logo{left:148px;top:2708px;font-family:var(--head);font-weight:500;font-size:19px;color:var(--mint);display:flex;align-items:center;gap:8px}
.foot-logo .mark{width:14px;height:14px;background:var(--mint)}
.socials{left:147px;top:2743px;display:flex;gap:4px}
.socials span{width:10px;height:10px;border-radius:50%;background:#fff}
.contact-row{position:absolute;left:148px;display:flex;gap:14px;font-size:10.5px;line-height:14px}
.contact-row svg{flex:none;margin-top:1px}
.copy{left:152px;top:2900px;font-size:8.5px;color:#dff}
.fcol{position:absolute;top:2740px;font-size:10.5px}
.fcol h5{font-weight:500;font-size:10.5px;margin-bottom:14px}
.fcol li{list-style:none;line-height:14.3px;color:#e6fffb}
</style>
</head>
<body>

<!-- hero -->
<div class="abs hero-bg" role="img" aria-label="Dark blurred technical blueprint of machine parts"></div>
<div class="vline" style="left:50px;top:0;height:2321px"></div>
<div class="vline" style="left:425px;top:0;height:437px"></div>
<div class="vline" style="left:800px;top:0;height:437px"></div>
<div class="vline" style="left:1150px;top:50px;height:2271px"></div>

<div class="abs nav-logo"><span class="mark"></span>QR.KA Horizon</div>
<nav class="abs nav"><a class="active" href="#">Home</a><a href="#">Solutions</a><a href="#">About us</a></nav>
<div class="abs nav-contact">Contact</div>

<div class="abs hero-copy">
  <div class="eyebrow">Stand for Imagination</div>
  <h1 class="hero-title">QR.KA Horizon: Where<br>Engineering Software<br>Meets IT Excellence</h1>
  <p class="hero-text">QR.KA Horizon bridges the complexity between engineering software and IT systems into one unified, streamlined experience. It empowers teams to collaborate better, automate faster, and deliver smarter with seamless integration across every layer of development and operations.</p>
  <div class="btn hero-btn"><span class="ico"><i style="left:4px;top:0"></i><i style="left:0;top:7px"></i><i style="left:8px;top:7px"></i></span>Try it for FREE</div>
</div>

<!-- feature cards -->
<div class="abs cards-strip"></div>
<div class="abs feature" style="left:50px;width:375px"><h3><span class="ico"></span>Seamless Integration</h3><p>Connect engineering software and IT infrastructure effortlessly in one unified platform, eliminating data silos and manual handovers.</p><span class="brand-ghost">QR.KA Horizon</span></div>
<div class="vline" style="left:425px;top:437px;height:194px;background:#1d4a46"></div>
<div class="abs feature" style="left:426px;width:374px"><h3><span class="ico"></span>Automated Workflows</h3><p>Streamline complex processes with intelligent automation—from code deployment to infrastructure updates—saving time while reducing human error.</p><span class="brand-ghost">QR.KA Horizon</span></div>
<div class="abs feature light" style="left:800px;width:325px"><h3><span class="ico"></span>Real-Time Collaboration</h3><p>Enable dev and IT teams to work in sync with shared dashboards, live updates, and instant feedback loops for faster, smarter decision-making.</p><span class="brand-ghost">QR.KA Horizon</span></div>

<div class="abs scroll">SCROLL TO EXPLORE</div>
<div class="abs scroll-pill"></div>

<!-- story -->
<div class="abs code-band" role="img" aria-label="Blurred lines of code on a dark screen"></div>
<div class="hline" style="left:0;top:733px;width:1200px"></div>
<div class="abs story-photo" role="img" aria-label="Close-up of a code editor listing project files"></div>
<div class="vline" style="left:102px;top:733px;height:351px"></div>
<div class="abs side-num" style="left:60px;top:770px">2/04</div>
<span class="dot" style="left:74px;top:884px"></span>
<span class="dot" style="left:74px;top:919px"></span>
<svg class="ring" style="left:65px;top:955px" viewBox="0 0 22 22"><circle cx="11" cy="11" r="9" fill="none" stroke="#00bba5" stroke-width="1.6" stroke-dasharray="46 11"/><circle cx="11" cy="11" r="2" fill="#00bba5"/></svg>
<span class="dot" style="left:74px;top:1008px"></span>
<div class="abs story-panel"></div>
<div class="abs section-label story-label">From Frustration to Innovation</div>
<h2 class="abs story-title">How one team’s challenge became a universal solution.</h2>
<div class="abs story-text">
<p>QR.KA Horizon was born out of a simple yet powerful realization: software engineers and IT professionals often work toward the same goals, but with tools and workflows that keep them apart. Our founding team—made up of developers, system architects, and DevOps specialists—felt the pain of this disconnect firsthand. After countless hours juggling between code, infrastructure, and misaligned tools, they decided to build a solution that would bring everything (and everyone) together.</p>
<p>What began as an internal project soon evolved into a platform embraced by teams facing the same struggles around the world. Today, QR.KA Horizon empowers organizations to break silos, streamline operations, and foster true collaboration between engineering and IT. We believe that when tools—and people—communicate seamlessly, amazing things happen.</p>
</div>
<div class="abs story-link">Discover more about our story
<svg width="10" height="10" viewBox="0 0 10 10"><path d="M2 1l2 2-1 1c.6 1.3 1.7 2.4 3 3l1-1 2 2-1.5 1.5C4.5 9 1 5.5.5 2.5z" fill="#fff"/></svg></div>
<div class="hline" style="left:0;top:1084px;width:1200px"></div>
<div class="abs strip2"></div>
<div class="abs strip2-photo" role="img" aria-label="Blurred code lines continuing"></div>

<!-- solutions -->
<div class="abs section-label sol-label">Our Solutions</div>
<h2 class="abs sol-title">Streamline collaboration between software engineering and IT with an all-in-one integration platform. Automate workflows, reduce silos, and accelerate delivery.</h2>
<div class="abs side-num" style="left:60px;top:1346px">3/04</div>
<span class="dot" style="left:74px;top:1461px"></span>
<svg class="ring" style="left:65px;top:1497px" viewBox="0 0 22 22"><circle cx="11" cy="11" r="9" fill="none" stroke="#00bba5" stroke-width="1.6" stroke-dasharray="46 11"/><circle cx="11" cy="11" r="2" fill="#00bba5"/></svg>
<span class="dot" style="left:74px;top:1551px"></span>
<span class="dot" style="left:74px;top:1586px"></span>

<div class="abs sol-card" style="left:144px"><div class="num">01</div><h4>Integrated Engineering &amp; IT Operations</h4><p>QR.KA Horizon seamlessly connects software engineering processes with IT infrastructure. This integration ensures that development and operations are always aligned, reducing friction and miscommunication. Teams can now move from planning to deployment without disruptions.</p><div class="more">Learn more <i></i></div></div>
<div class="vline" style="left:442px;top:1344px;height:320px;background:#333"></div>
<div class="abs sol-card" style="left:461px"><div class="num">02</div><h4>End-to-End Process<br>Automation</h4><p>From code commit to production deployment, QR.KA Horizon automates the entire lifecycle. This reduces the need for manual intervention and improves delivery speed. You gain more time to focus on building quality products, not managing processes.</p><div class="more">Learn more <i></i></div></div>
<div class="abs sol-card sol-photo" role="img" aria-label="Engineers working at desks with monitors, tinted teal"><div class="num">03</div><h4>End-to-End Process<br>Automation</h4><p>From code commit to production deployment, QR.KA Horizon automates the entire lifecycle. This reduces the need for manual intervention and improves delivery speed. You gain more time to focus on building quality products, not managing processes.</p><div class="more" style="left:19px">Learn more <i></i></div></div>

<!-- integration section -->
<div class="abs side-strip"></div>
<div class="hline" style="left:106px;top:1767px;width:1044px"></div>
<div class="vline" style="left:106px;top:1767px;height:554px"></div>
<div class="vline" style="left:277px;top:1767px;height:251px"></div>
<div class="vline" style="left:581px;top:1767px;height:554px"></div>
<div class="hline" style="left:106px;top:2018px;width:475px"></div>
<div class="abs side-num" style="left:60px;top:1922px">4/04</div>
<svg class="ring" style="left:65px;top:2036px" viewBox="0 0 22 22"><circle cx="11" cy="11" r="9" fill="none" stroke="#00bba5" stroke-width="1.6" stroke-dasharray="46 11"/><circle cx="11" cy="11" r="2" fill="#00bba5"/></svg>
<span class="dot" style="left:74px;top:2091px"></span>
<span class="dot" style="left:74px;top:2126px"></span>
<span class="dot" style="left:74px;top:2161px"></span>

<div class="abs eng-label">Detail Engineering Design</div>
<div class="thumb" style="left:134px;top:1822px" role="img" aria-label="Engineering drawing thumbnail"></div>
<div class="thumb" style="left:134px;top:1900px" role="img" aria-label="Wireframe machine model thumbnail"></div>
<div class="abs eng-more">2+</div>
<div class="abs eng-drawing" role="img" aria-label="White wireframe 3D model of an industrial plant"></div>

<div class="abs code-label">Coding Sources</div>
<div class="abs code-shot" role="img" aria-label="Developer tools window showing source code">
  <span class="bar" style="left:0;top:0;width:407px;height:10px;background:#2a3345"></span>
  <span class="bar" style="left:10px;top:20px;width:160px"></span>
  <span class="bar" style="left:18px;top:30px;width:230px;background:#6a8b6e"></span>
  <span class="bar" style="left:18px;top:40px;width:190px"></span>
  <span class="bar" style="left:26px;top:50px;width:250px;background:#8c6f4c"></span>
  <span class="bar" style="left:26px;top:60px;width:210px"></span>
  <span class="bar" style="left:18px;top:70px;width:240px;background:#6a8b6e"></span>
  <span class="bar" style="left:26px;top:80px;width:170px"></span>
  <span class="bar" style="left:26px;top:90px;width:220px;background:#8c6f4c"></span>
  <span class="bar" style="left:18px;top:100px;width:200px"></span>
  <span class="bar" style="left:10px;top:110px;width:150px;background:#6a8b6e"></span>
  <span class="bar" style="left:10px;top:120px;width:120px"></span>
  <span class="bar" style="left:310px;top:0;width:1px;height:135px;background:#3a4458"></span>
  <span class="bar" style="left:318px;top:24px;width:70px"></span>
  <span class="bar" style="left:318px;top:44px;width:55px;background:#6a8b6e"></span>
  <span class="bar" style="left:318px;top:64px;width:75px"></span>
  <span class="bar" style="left:318px;top:84px;width:60px;background:#8c6f4c"></span>
</div>
<div class="abs btn try-btn"><span class="ico"><i style="left:4px;top:0"></i><i style="left:0;top:7px"></i><i style="left:8px;top:7px"></i></span>Try NOW</div>

<div class="abs section-label int-label">Where Code Meets Infrastructure—Perfectly</div>
<h2 class="abs int-title">QR.KA Horizon isn’t just a tool—it’s the missing link between engineering precision and IT reliability. Every feature is designed to eliminate friction, boost collaboration, and unlock your team’s full potential.</h2>
<div class="abs acc">
  <div class="acc-row open"><span class="sq" style="width:24px;height:10px;background:#fff"></span>Adaptive Infrastructure Sync</div>
  <div class="acc-body">Automate the entire journey from code commit to live deployment. QR.KA Horizon syncs your repos, builds, tests, and infrastructure provisioning in one seamless flow. Save time, reduce human error, and ship with confidence.</div>
  <div class="acc-row"><span class="sq"></span>Smart Resource Allocation</div>
  <div class="acc-row"><span class="sq"></span>Scalable Deployment Engine</div>
</div>

<!-- CTA -->
<div class="abs cta-bg"></div>
<div class="abs city" role="img" aria-label="Wireframe city skyline in light teal lines"></div>
<div class="abs cta-ghost">QR.KA Horizon</div>
<h2 class="abs cta-title">Ready to bring your engineering and IT teams together? Let QR.KA Horizon simplify the complex—so you can build, ship, and scale with confidence.</h2>
<div class="abs btn cta-btn"><span class="ico"><i style="left:4px;top:0"></i><i style="left:0;top:7px"></i><i style="left:8px;top:7px"></i></span>Try it for FREE</div>

<!-- footer -->
<div class="abs foot-overlay"></div>
<div class="abs foot-panel"></div>
<div class="abs foot-logo"><span class="mark"></span>QR.KA Horizon</div>
<div class="abs socials"><span></span><span></span><span></span><span></span></div>
<div class="contact-row" style="top:2778px"><svg width="12" height="11" viewBox="0 0 12 11"><path d="M0 1h12v9H0z" fill="none" stroke="#fff" stroke-width="1.4"/><path d="M0 1l6 5 6-5" fill="none" stroke="#fff" stroke-width="1.4"/></svg>hello@qrkahorizon.com</div>
<div class="contact-row" style="top:2807px"><svg width="12" height="12" viewBox="0 0 10 10"><path d="M2 1l2 2-1 1c.6 1.3 1.7 2.4 3 3l1-1 2 2-1.5 1.5C4.5 9 1 5.5.5 2.5z" fill="#fff"/></svg>+00 222 45 67 89</div>
<div class="contact-row" style="top:2836px"><svg width="12" height="14" viewBox="0 0 12 14" style="margin-top:12px"><path d="M6 0a5 5 0 0 1 5 5c0 4-5 9-5 9S1 9 1 5a5 5 0 0 1 5-5z" fill="#fff"/><circle cx="6" cy="5" r="2" fill="#0f8f82"/></svg><span>Lindenhof, Nordquartier<br>48210 Westmark<br>Valoria</span></div>
<div class="abs copy">Copyright © 2025 QR.KA Horizon.</div>

<div class="fcol" style="left:799px"><h5>Quick Links</h5><ul><li>Home</li><li>Features</li><li>Our Story</li><li>Contact</li><li>FAQ</li></ul></div>
<div class="fcol" style="left:890px"><h5>Resources</h5><ul><li>Documentation</li><li>Blog / Insights</li><li>Support Center</li><li>System Status</li></ul></div>
<div class="fcol" style="left:999px"><h5>Product</h5><ul><li>Features</li><li>Integrations</li><li>Documentation</li><li>Roadmap</li></ul></div>

</body>
</html>
```